Unique Playing Card Deck Design

Brief:

I am looking for a designer to design a whole deck of cards from the ground up. I would like both the front and back designed for the deck, and would like the desk to include all the standard cards including jokers. I would like to make each card as unique as possible, so including original designs and artwork for the non-face cards as well.

I would like these cards to be poker size (63mm x 88mm, 2.5" x 3.5") or B8 size according to ISO 216) and I’ve attached a template that should be followed for the sizing.

No real limit on the design so be as creative as you can!

Design Details

Color Mode: RGB or CYMK for color images, Grayscale for black and white

File types: JPG, BMP, PNG, GIF, TIFF

Image resolution: Minimum 300 dpi

Bleeding: Allow 1/8" (approx 36 pixels based on a 300dpi image) for bleeding and a further 1/8" for safe area margin inside each side

EDIT: Because this project requires a lot of design work I am fine for the submissions to be limited to 3 or 4 cards that would demonstrate the overall direction that you are taking. Once I have chosen the designs we can continue refining them and adding the rest of the deck. I would also like a box for the cards to be designed and can provide a template after I have chosen the designers. Thanks and please let me know if you have any questions!

EDIT2: I realize this project is a lot of work and so I have taken the amounts that I had for 2nd and 3rd place and increased the reward for 1st place. I am still interested in selecting multiple designs, but because this project is being done on a committed payment basis I wanted to ensure that I was only obligated to select one design. However, if there are multiple designs that I am interested in, I will award the design work to an additional 1-3 designers (to a maximum of 4 total) on the same terms as 1st place. i.e. all designers selected will be paid the same amount. Thanks again for looking!

Target Market(s)

Adult card players who appreciate good design (i.e. the designs should not be cartoon-like or targeted at children). These are going to be premium cards printed on the best quality paper etc so I would like the design to reflect this.

Font styles to use
Decorative
Script

Requirements
Nice to have
• I will leave the design idea up to you but I like the look of really old playing cards (think of a deck of medieval playing cards for example). I also like the art deco kind of aesthetic. On the complete opposite side of the spectrum a very modern looking, minimalist design is also appealing.
• These are just a few ideas but as I said I am really open to anything. It just needs to be a bold, original design.

```html
<!DOCTYPE html>
<html lang="en">
<head>
<meta charset="utf-8">
<title>Ten of Spades</title>
<link rel="stylesheet" href="https://fonts.googleapis.com/css2?family=Tinos:wght@700&display=swap">
<style>
  :root {
    --card-red: #d0302a;
    --ink: #111111;
    --paper: #ffffff;
    --gold: #fedd45;
    --edge: #8fd3ea;
  }
  html, body {
    margin: 0;
    padding: 0;
    width: 831px;
    height: 1200px;
    overflow: hidden;
    background: var(--paper);
  }
  .card {
    position: relative;
    width: 831px;
    height: 1200px;
    background: var(--paper);
    border: 1px solid var(--edge);
    border-radius: 14px;
    box-sizing: border-box;
    overflow: hidden;
  }
  .card-art {
    position: absolute;
    inset: 0;
  }
  .cell {
    position: absolute;
    box-sizing: border-box;
  }
  .cell--red { background: var(--card-red); }
  .cell--gold { background: var(--gold); }
  .cell--pip {
    background: var(--paper);
    border: 5px solid var(--gold);
    display: flex;
    align-items: center;
    justify-content: center;
  }
  .cell--plain {
    background: transparent;
    display: flex;
    align-items: center;
    justify-content: center;
  }
  .rank {
    font-family: "Tinos", "Times New Roman", serif;
    font-weight: 700;
    font-size: 142px;
    line-height: 1;
    color: var(--ink);
    letter-spacing: -6px;
    margin-top: 6px;
  }
</style>
</head>
<body>
<div class="card">
  <svg class="card-art" width="831" height="1200" viewBox="0 0 831 1200" aria-hidden="true">
    <defs>
      <path id="spade" d="M50 0 C30 30 0 45 0 66 C0 84 22 92 41 78 C39 90 33 97 24 100 L76 100 C67 97 61 90 59 78 C78 92 100 84 100 66 C100 45 70 30 50 0 Z"/>
    </defs>
    <rect class="card-field" x="42" y="46" width="753" height="1109" fill="var(--card-red)"/>
    <use href="#spade" transform="translate(79 90) scale(0.7 0.92)" fill="var(--ink)"/>
    <use href="#spade" transform="translate(668 90) scale(0.7 0.92)" fill="var(--ink)"/>
    <use href="#spade" transform="translate(79 1025) scale(0.7 0.92)" fill="var(--ink)"/>
    <use href="#spade" transform="translate(668 1025) scale(0.7 0.92)" fill="var(--ink)"/>
    <g fill="var(--ink)">
      <use href="#spade" transform="translate(227 80) scale(0.17 0.2)"/>
      <use href="#spade" transform="translate(258 80) scale(0.17 0.2)"/>
      <use href="#spade" transform="translate(288 80) scale(0.17 0.2)"/>
      <use href="#spade" transform="translate(319 80) scale(0.17 0.2)"/>
      <use href="#spade" transform="translate(349 80) scale(0.17 0.2)"/>
      <use href="#spade" transform="translate(380 80) scale(0.17 0.2)"/>
      <use href="#spade" transform="translate(410 80) scale(0.17 0.2)"/>
      <use href="#spade" transform="translate(441 80) scale(0.17 0.2)"/>
      <use href="#spade" transform="translate(471 80) scale(0.17 0.2)"/>
      <use href="#spade" transform="translate(502 80) scale(0.17 0.2)"/>
      <use href="#spade" transform="translate(532 80) scale(0.17 0.2)"/>
      <use href="#spade" transform="translate(563 80) scale(0.17 0.2)"/>
      <use href="#spade" transform="translate(593 80) scale(0.17 0.2)"/>
      <use href="#spade" transform="translate(624 80) scale(0.17 0.2)"/>
      <use href="#spade" transform="translate(222 1101) scale(0.17 0.2)"/>
      <use href="#spade" transform="translate(253 1101) scale(0.17 0.2)"/>
      <use href="#spade" transform="translate(283 1101) scale(0.17 0.2)"/>
      <use href="#spade" transform="translate(314 1101) scale(0.17 0.2)"/>
      <use href="#spade" transform="translate(344 1101) scale(0.17 0.2)"/>
      <use href="#spade" transform="translate(375 1101) scale(0.17 0.2)"/>
      <use href="#spade" transform="translate(405 1101) scale(0.17 0.2)"/>
      <use href="#spade" transform="translate(436 1101) scale(0.17 0.2)"/>
      <use href="#spade" transform="translate(466 1101) scale(0.17 0.2)"/>
      <use href="#spade" transform="translate(497 1101) scale(0.17 0.2)"/>
      <use href="#spade" transform="translate(527 1101) scale(0.17 0.2)"/>
      <use href="#spade" transform="translate(558 1101) scale(0.17 0.2)"/>
      <use href="#spade" transform="translate(588 1101) scale(0.17 0.2)"/>
      <use href="#spade" transform="translate(619 1101) scale(0.17 0.2)"/>
    </g>
    <path class="panel-frame"
      d="M206 128 L630 128 A82 82 0 0 0 712 210 L712 993 A82 82 0 0 0 630 1075 L206 1075 A82 82 0 0 0 124 993 L124 210 A82 82 0 0 0 206 128 Z"
      fill="var(--paper)" stroke="var(--ink)" stroke-width="24"/>
    <polygon points="505,237 542,345 670,377 505,377" fill="var(--gold)"/>
    <polygon points="157,866 280,900 315,1008 315,866" fill="var(--gold)"/>
  </svg>

  <!-- row 1 -->
  <div class="cell cell--pip" style="left:155px;top:235px;width:162px;height:144px;"><span class="rank">10</span></div>
  <div class="cell cell--red" role="img" aria-label="Red tile with a white line ornament of overlapping squares" style="left:317px;top:237px;width:188px;height:141px;"></div>

  <!-- row 2 -->
  <div class="cell cell--red" style="left:157px;top:393px;width:158px;height:142px;"></div>
  <div class="cell cell--pip" style="left:315px;top:393px;width:192px;height:144px;"><span class="rank">10</span></div>
  <div class="cell cell--red" style="left:507px;top:393px;width:163px;height:142px;"></div>

  <!-- row 3 -->
  <div class="cell cell--gold" role="img" aria-label="Gold emblem tile with red circle and crossed ellipses" style="left:157px;top:550px;width:158px;height:143px;border:6px solid var(--card-red);"></div>
  <div class="cell cell--red" style="left:315px;top:550px;width:192px;height:142px;"></div>
  <div class="cell cell--pip" style="left:505px;top:548px;width:168px;height:145px;"><span class="rank">10</span></div>

  <!-- row 4 -->
  <div class="cell cell--pip" style="left:155px;top:706px;width:162px;height:146px;"><span class="rank">10</span></div>
  <div class="cell cell--gold" style="left:317px;top:708px;width:190px;height:142px;"></div>
  <div class="cell cell--red" style="left:507px;top:708px;width:163px;height:142px;">
    <svg width="163" height="142" viewBox="0 0 163 142" aria-hidden="true">
      <rect x="22" y="20" width="119" height="102" fill="none" stroke="var(--ink)" stroke-width="13"/>
      <rect x="34" y="32" width="95" height="78" fill="none" stroke="var(--gold)" stroke-width="11"/>
    </svg>
  </div>

  <!-- row 5 -->
  <div class="cell cell--red" style="left:315px;top:866px;width:190px;height:142px;"></div>
  <div class="cell cell--plain" style="left:505px;top:866px;width:165px;height:142px;"><span class="rank">10</span></div>
</div>
</body>
</html>
```